Business Card and Stationary for an Executive and Life Coaching company
Harvest Kindle
Simple
Lina Morvel, QLT, RDH
Executive Life Coach
2275 Wexbury Ln. Suite 318
Corvale, GA 30917
Lina@HarvestKindle.com
www.HarvestKindle.com
I've included logo for QLT, and instructions on where and how to place it.
I'd like the design to be simple and uncluttered, while enticing people to want to be part of the movement and program because it is fun, smart, and provides tangible and positive results.
I'd like simple but unique fonts.
ascend to abundance (on top)
(1 letter logo may go in the middle)
Success Coach to Smart Professionals and Entrepreneurs. (bottom of card)

```html
<!DOCTYPE html>
<html lang="en">
<head>
<meta charset="utf-8">
<title>Harvest Kindle Stationery</title>
<link href="https://fonts.googleapis.com/css2?family=Montserrat:wght@400;500;700&display=swap" rel="stylesheet">
<style>
  :root {
    --sage: #5a6b54;
    --sage-dark: #4b5b46;
    --gold: #a98c5a;
    --paper: #ffffff;
    --ink: #4a4f48;
    --backdrop: #e3e5e2;
  }
  * { box-sizing: border-box; margin: 0; padding: 0; }
  html, body { width: 1200px; height: 1011px; overflow: hidden; }
  body {
    background: var(--backdrop);
    font-family: "Montserrat", Arial, sans-serif;
    color: var(--ink);
    position: relative;
  }
  .sheet { position: absolute; background: var(--paper); box-shadow: 0 6px 18px rgba(0,0,0,.15); overflow: hidden; }
  .brand { font-weight: 700; color: var(--sage); letter-spacing: .5px; display: flex; align-items: center; gap: 8px; white-space: nowrap; }
  .brand-square { width: 14px; height: 14px; background: var(--gold); flex: none; }
  .small { font-size: 9px; line-height: 1.5; color: var(--ink); white-space: nowrap; }
  .band { position: absolute; left: 0; right: 0; bottom: 0; background: var(--sage); }
  .band-gold { position: absolute; left: 0; right: 0; background: var(--gold); }
  .web { position: absolute; color: #fff; font-size: 9px; letter-spacing: .5px; white-space: nowrap; }

  /* Letterhead */
  .letterhead { left: 80px; top: 130px; width: 460px; height: 650px; }
  .letterhead .brand { position: absolute; left: 40px; top: 40px; font-size: 22px; }
  .letterhead .address { position: absolute; right: 40px; top: 40px; text-align: left; }
  .letterhead .band { height: 46px; }
  .letterhead .band-gold { bottom: 46px; height: 4px; }
  .letterhead .web { left: 40px; bottom: 17px; }

  /* Envelope */
  .envelope { left: 600px; top: 70px; width: 520px; height: 260px; }
  .envelope .brand { position: absolute; left: 30px; top: 30px; font-size: 20px; }
  .envelope .address { position: absolute; left: 30px; top: 72px; }
  .envelope .band { height: 30px; }
  .envelope .band-gold { bottom: 30px; height: 4px; }
  .envelope .web { right: 30px; bottom: 10px; }

  /* Card back */
  .card-back { left: 600px; top: 380px; width: 420px; height: 240px; background: var(--sage); }
  .card-back .motto { position: absolute; top: 28px; left: 0; right: 0; text-align: center; color: #fff; font-size: 12px; letter-spacing: 1px; }
  .card-back .brand { position: absolute; top: 100px; left: 0; right: 0; justify-content: center; color: #fff; font-size: 24px; }
  .card-back .tagline { position: absolute; bottom: 22px; left: 0; right: 0; text-align: center; color: #fff; font-size: 9px; }

  /* Card front */
  .card-front { left: 600px; top: 670px; width: 420px; height: 240px; }
  .card-front .brand { position: absolute; left: 26px; top: 70px; font-size: 20px; }
  .card-front .details { position: absolute; left: 230px; top: 26px; }
  .card-front .name { font-size: 13px; font-weight: 700; color: var(--sage); }
  .card-front .role { font-size: 9px; margin-bottom: 10px; }
  .card-front .band { height: 28px; }
  .card-front .band-gold { bottom: 28px; height: 3px; }
  .card-front .web { right: 20px; bottom: 9px; }
  .contact-line { display: flex; align-items: center; gap: 6px; }
  .contact-line svg { flex: none; }
  .gap-after { margin-bottom: 8px; }
</style>
</head>
<body>

<section class="sheet letterhead">
  <div class="brand"><span class="brand-square"></span>Harvest Kindle</div>
  <div class="address small">2275 Wexbury Ln. Suite 318<br>Corvale, GA 30917<br>555 014 2290<br>555 014 7731</div>
  <div class="band-gold"></div>
  <div class="band"></div>
  <div class="web">www.HarvestKindle.com</div>
</section>

<section class="sheet envelope">
  <div class="brand"><span class="brand-square"></span>Harvest Kindle</div>
  <div class="address small">2275 Wexbury Ln. Suite 318<br>Corvale, GA 30917</div>
  <div class="band-gold"></div>
  <div class="band"></div>
  <div class="web">www.HarvestKindle.com</div>
</section>

<section class="sheet card-back">
  <div class="motto">ascend to abundance</div>
  <div class="brand">Harvest Kindle</div>
  <div class="tagline">Success Coach to Smart Professionals and Entrepreneurs.</div>
</section>

<section class="sheet card-front">
  <div class="brand"><span class="brand-square"></span>Harvest Kindle</div>
  <div class="details small">
    <div class="name">Lina Morvel, QLT, RDH</div>
    <div class="role">Executive Life Coach</div>
    <div>2275 Wexbury Ln. Suite 318</div>
    <div class="gap-after">Corvale, GA 30917</div>
    <div class="contact-line">
      <svg width="9" height="9" viewBox="0 0 10 10"><circle cx="5" cy="5" r="5" fill="var(--sage)"/></svg>555 014 2290
    </div>
    <div class="contact-line">
      <svg width="9" height="9" viewBox="0 0 10 10"><circle cx="5" cy="5" r="5" fill="var(--sage)"/></svg>555 014 7731
    </div>
    <div class="contact-line">
      <svg width="9" height="9" viewBox="0 0 10 10"><circle cx="5" cy="5" r="5" fill="var(--sage)"/></svg>Lina@HarvestKindle.com
    </div>
  </div>
  <div class="band-gold"></div>
  <div class="band"></div>
  <div class="web">www.HarvestKindle.com</div>
</section>

</body>
</html>
```